Concierge Healthcare Business Card Design and Logo

We need a logo and business card design for a new company called "Sound Haven". We will provide concierge audiological care, hearing aids, hearing exams, custom hearing protection etc to patients in the comfort of their homes and offices. We would like a sleek and modern design preferably with an Ear related logo.

Target Market(s)

People with hearing loss, Hunters, Musicians
My usual clientele are older individuals so usually 50+ years old

Industry/Entity Type

Health Care

Contact Information for Business Card

Celia Brandt, AuD
Audiologist
512-648-2917
soundhaven@mailvoro.com
www.soundhaven-vorel.com

Logo Text

Sound Haven

Number of Pages Required

3 page

```html
<!DOCTYPE html>
<html lang="en">
<head>
<meta charset="utf-8">
<title>Sound Haven — Business Card</title>
<link rel="stylesheet" href="https://fonts.googleapis.com/css2?family=Jost:wght@500;600&family=Questrial&display=swap">
<style>
  :root {
    --backdrop: #2b2c2b;
    --paper: #f6f6f5;
    --brand-blue: #1f6db5;
    --deep-blue: #0b4a7e;
    --glow-blue: #1d72bd;
    --ink: #1d1d1d;
    --white: #ffffff;
  }
  * { box-sizing: border-box; margin: 0; padding: 0; }
  html, body {
    width: 1200px; height: 1200px; overflow: hidden;
    background: var(--backdrop);
  }
  .card-pair {
    position: absolute; top: 445px; left: 88px;
    display: flex; gap: 14px;
  }
  .card {
    position: relative; width: 505px; height: 294px; overflow: hidden;
  }
  .card--front { background: var(--paper); }
  .card--back {
    background: radial-gradient(ellipse 55% 65% at 50% 45%, var(--glow-blue) 0%, #145e9e 45%, var(--deep-blue) 100%);
  }
  .wordmark {
    position: absolute; display: flex; align-items: center;
    font-family: "Jost", sans-serif; font-weight: 600; letter-spacing: 0.5px;
  }
  .wordmark__ring { flex: none; }
  .card--front .wordmark {
    left: 24px; top: 36px; font-size: 30px; gap: 10px; color: var(--brand-blue);
  }
  .card--back .wordmark {
    left: 0; right: 0; top: 106px; justify-content: center;
    font-size: 36px; gap: 12px; color: var(--white);
  }
  .contact {
    position: absolute; right: 27px; top: 172px; text-align: right;
    font-family: "Questrial", sans-serif; color: var(--ink);
  }
  .contact__name {
    font-family: "Jost", sans-serif; font-weight: 600; font-size: 16.5px;
    color: var(--brand-blue); line-height: 20px;
  }
  .contact__role { font-size: 13.5px; line-height: 16px; }
  .contact__list { list-style: none; margin-top: 14px; }
  .contact__item {
    display: flex; align-items: center; justify-content: flex-end; gap: 5px;
    font-size: 13.5px; line-height: 17.5px;
  }
  .contact__accent { color: var(--brand-blue); }
  .contact__icon { width: 11px; height: 11px; flex: none; }
  .back-url {
    position: absolute; left: 0; right: 0; top: 253px; text-align: center;
    font-family: "Questrial", sans-serif; font-size: 13.5px; color: #dfe8f2;
    letter-spacing: 0.3px;
  }
</style>
</head>
<body>
  <main class="card-pair">
    <section class="card card--front">
      <div class="wordmark">
        <span>SOUND</span>
        <svg class="wordmark__ring" width="40" height="40" viewBox="0 0 40 40"><circle cx="20" cy="20" r="18" fill="none" stroke="#1f6db5" stroke-width="1.5"/></svg>
        <span>HAVEN</span>
      </div>
      <div class="contact">
        <p class="contact__name">Celia Brandt, AuD</p>
        <p class="contact__role">Audiologist</p>
        <ul class="contact__list">
          <li class="contact__item">512-648-2917
            <svg class="contact__icon" viewBox="0 0 11 11"><rect width="11" height="11" rx="1.5" fill="#1f6db5"/><path d="M3 3.2c0 2.6 2.2 4.8 4.8 4.8l.6-1.2-1.4-.8-.6.6c-.9-.4-1.5-1-1.9-1.9l.6-.6-.8-1.4z" fill="#fff"/></svg>
          </li>
          <li class="contact__item">soundhaven@mailvoro.com
            <svg class="contact__icon" viewBox="0 0 11 11"><rect width="11" height="11" rx="1.5" fill="#1f6db5"/><rect x="2.3" y="3.3" width="6.4" height="4.4" fill="none" stroke="#fff" stroke-width="0.9"/><path d="M2.3 3.3l3.2 2.4 3.2-2.4" fill="none" stroke="#fff" stroke-width="0.9"/></svg>
          </li>
          <li class="contact__item"><span>www.<span class="contact__accent">soundhaven-vorel</span>.com</span>
            <svg class="contact__icon" viewBox="0 0 11 11"><rect width="11" height="11" rx="1.5" fill="#1f6db5"/><circle cx="5.5" cy="5.5" r="3" fill="none" stroke="#fff" stroke-width="0.9"/><path d="M2.5 5.5h6M5.5 2.5v6" stroke="#fff" stroke-width="0.7"/></svg>
          </li>
        </ul>
      </div>
    </section>
    <section class="card card--back">
      <div class="wordmark">
        <span>SOUND</span>
        <svg class="wordmark__ring" width="48" height="48" viewBox="0 0 48 48"><circle cx="24" cy="24" r="22" fill="none" stroke="#ffffff" stroke-width="1.5"/></svg>
        <span>HAVEN</span>
      </div>
      <p class="back-url">www.soundhaven-vorel.com</p>
    </section>
  </main>
</body>
</html>
```